Etikett für einen Rosé Wein
Zielgruppe
Wir sind ein Weingut und benötigen ein neues Etikett für unseren Muskattrollinger Rosé. Unsere Kunden sind eher traditionelle Weinkäufer.
Aufgabenstellung
Format:
Höhe: 9 cm
Breite: 11 cm
Da es nur ein Vorderetikett gibt, müssen alle relevanten Angaben (Hersteller, Alkohol, Inhalt in L, Rebsorte, etc.) enthalten sein. (siehe Flaschenabbildung anbei)
WÜRTTEMBERG
2019er
Muskattrollinger Rosé
DEUTSCHER QUALITÄTSWEIN
11,0 % Vol.
0,75 l
Enthält Sulfite
A.P.Nr. 58127364
Abfüller
Straße / PLZ / Ort / Tel.
Der Flaschenverschluss ist schwarz d.h. das neue Etikettendesign sollte dazu passen.
Bisher ist der Hintergrund des Weinetiketts schwarz. Dies muss jedoch nicht so bleiben.
Im Anhang finden Sie außerdem ein Plakat. Ggf. können Sie für das Flaschendesign einige nostalgische Elemente davon übernehmen.

```html
<!DOCTYPE html>
<html lang="de">
<head>
<meta charset="utf-8">
<title>Muskattrollinger Rosé – Etikett</title>
<link href="https://fonts.googleapis.com/css2?family=Playfair+Display:wght@400&family=Didact+Gothic&display=swap" rel="stylesheet">
<style>
  :root {
    --backdrop: #dcdbdd;
    --label-pink: #ecd7e6;
    --ink: #2a2627;
    --art-dark: #4a4546;
    --art-light: #b9adb4;
  }
  html, body {
    margin: 0;
    padding: 0;
    width: 1200px;
    height: 892px;
    overflow: hidden;
    background: var(--backdrop);
  }
  .wine-label {
    position: absolute;
    left: 100px;
    top: 37px;
    width: 1000px;
    height: 818px;
    background: var(--label-pink);
    color: var(--ink);
    font-family: "Didact Gothic", sans-serif;
    box-shadow: 0 2px 10px rgba(0,0,0,0.08);
  }
  .wine-label > * {
    position: absolute;
    margin: 0;
    line-height: 1;
    white-space: nowrap;
  }
  .centered {
    left: 0;
    right: 0;
    text-align: center;
  }
  .region {
    top: 34px;
    font-family: "Playfair Display", serif;
    font-size: 56px;
    letter-spacing: 3px;
    font-weight: 400;
  }
  .vintage {
    top: 98px;
    font-size: 34px;
    letter-spacing: 2px;
  }
  .variety {
    top: 148px;
    font-size: 46px;
    letter-spacing: 3px;
    font-weight: 400;
  }
  .label-art {
    top: 215px;
    left: 370px;
    width: 260px;
    height: 385px;
    background: linear-gradient(180deg, var(--art-light) 0%, var(--art-dark) 100%);
    border-radius: 50% 50% 8px 8px / 20% 20% 8px 8px;
    opacity: 0.75;
  }
  .quality {
    top: 625px;
    font-size: 34px;
    letter-spacing: 2px;
  }
  .ap-number {
    top: 668px;
    font-size: 24px;
    letter-spacing: 1.5px;
  }
  .bottler {
    top: 702px;
    font-size: 24px;
    letter-spacing: 1.5px;
  }
  .facts-left {
    top: 680px;
    left: 90px;
    font-size: 24px;
    letter-spacing: 1.5px;
    line-height: 1.35;
  }
  .facts-right {
    top: 680px;
    right: 90px;
    font-size: 24px;
    letter-spacing: 1.5px;
  }
  .address {
    top: 768px;
    font-size: 22px;
    letter-spacing: 2px;
    word-spacing: 8px;
  }
</style>
</head>
<body>
  <main class="wine-label">
    <h1 class="region centered">WÜRTTEMBERG</h1>
    <p class="vintage centered">2019er</p>
    <h2 class="variety centered">Muskattrollinger Rosé</h2>
    <div class="label-art" role="img" aria-label="Nostalgische Zeichnung: Mann mit Hut sitzt auf einem Weinfass und hebt ein Weinglas"></div>
    <p class="quality centered">DEUTSCHER QUALITÄTSWEIN</p>
    <p class="ap-number centered">A.P.Nr.&nbsp; 58127364</p>
    <p class="bottler centered">Abfüller</p>
    <p class="facts-left">11,0 % Vol.<br>Enthält Sulfite</p>
    <p class="facts-right">0,75 l</p>
    <p class="address centered">Straße / PLZ / Ort / Tel.</p>
  </main>
</body>
</html>
```